Dunmore Roofing

Want a professional looking business card

Industry/Entity Type

Business

Contact Information for Business Card

Paul Dunmore ( Owner) paul@dunmoreroofing-example.com, www.dunmoreroofing-example.com, Adress: 4172 Township road 43 Plantagenet,ON K9X4T2

```html
<!DOCTYPE html>
<html lang="en">
<head>
<meta charset="utf-8">
<title>Dunmore Roofing – Business Card</title>
<link rel="stylesheet" href="https://fonts.googleapis.com/css2?family=Montserrat:wght@400;500;600;700&display=swap">
<style>
  :root {
    --backdrop: #e8e3db;
    --card-clear: #eeece8;
    --card-edge: #d6d1c8;
    --navy: #1f4381;
    --navy-deep: #17366c;
    --brand-blue: #3b5688;
    --divider: #6f6a62;
    --text-light: #ddd6c8;
  }
  * { margin: 0; padding: 0; box-sizing: border-box; }
  html, body {
    width: 1200px;
    height: 1047px;
    overflow: hidden;
    background: var(--backdrop);
    font-family: "Montserrat", sans-serif;
  }
  .business-card {
    position: absolute;
    left: 120px;
    top: 263px;
    width: 960px;
    height: 520px;
    border-radius: 22px;
    overflow: hidden;
    background: var(--card-clear);
    border: 1px solid var(--card-edge);
    box-shadow: 0 14px 40px rgba(60, 50, 40, 0.18);
  }
  .brand-side {
    position: absolute;
    left: 0;
    top: 0;
    width: 451px;
    height: 100%;
    display: flex;
    align-items: center;
    justify-content: center;
    gap: 14px;
  }
  .brand-square {
    width: 22px;
    height: 22px;
    background: var(--brand-blue);
    flex: none;
  }
  .brand-name {
    color: var(--brand-blue);
    font-weight: 700;
    font-size: 30px;
    letter-spacing: 1px;
    text-transform: uppercase;
    white-space: nowrap;
  }
  .divider {
    position: absolute;
    left: 451px;
    top: 0;
    width: 4px;
    height: 100%;
    background: var(--divider);
  }
  .info-side {
    position: absolute;
    left: 458px;
    top: 0;
    right: 0;
    height: 100%;
    background: linear-gradient(160deg, var(--navy) 0%, var(--navy-deep) 100%);
    color: var(--text-light);
  }
  .notch {
    position: absolute;
    left: 0;
    top: 88px;
    width: 0;
    height: 0;
    border-top: 14px solid transparent;
    border-bottom: 14px solid transparent;
    border-left: 22px solid var(--text-light);
  }
  .person {
    position: absolute;
    left: 70px;
    top: 84px;
  }
  .person-name {
    font-size: 26px;
    font-weight: 600;
    letter-spacing: 1px;
    text-transform: uppercase;
  }
  .person-role {
    font-size: 20px;
    font-weight: 500;
    letter-spacing: 1px;
    text-transform: uppercase;
    margin-top: 4px;
  }
  .address {
    position: absolute;
    left: 70px;
    top: 266px;
    font-size: 18px;
    line-height: 29px;
    letter-spacing: 0.3px;
    white-space: nowrap;
  }
  .contacts {
    position: absolute;
    left: 70px;
    top: 352px;
    list-style: none;
    font-size: 18px;
    letter-spacing: 0.3px;
  }
  .contacts li {
    display: flex;
    align-items: center;
    height: 29px;
    white-space: nowrap;
  }
  .contacts svg {
    width: 16px;
    height: 16px;
    margin-right: 20px;
    fill: var(--text-light);
    flex: none;
  }
</style>
</head>
<body>
  <div class="business-card">
    <div class="brand-side">
      <span class="brand-square"></span>
      <span class="brand-name">Dunmore Roofing</span>
    </div>
    <div class="divider"></div>
    <div class="info-side">
      <span class="notch"></span>
      <div class="person">
        <p class="person-name">Paul Dunmore</p>
        <p class="person-role">Owner</p>
      </div>
      <p class="address">4172 Township road 43<br>Larkfield, WX K9X4T2</p>
      <ul class="contacts">
        <li>
          <svg viewBox="0 0 24 24" aria-hidden="true"><path d="M6.6 10.8c1.4 2.8 3.8 5.1 6.6 6.6l2.2-2.2c.3-.3.7-.4 1-.2 1.1.4 2.3.6 3.6.6.6 0 1 .4 1 1V20c0 .6-.4 1-1 1C10.6 21 3 13.4 3 4c0-.6.4-1 1-1h3.5c.6 0 1 .4 1 1 0 1.3.2 2.5.6 3.6.1.3 0 .7-.2 1z"/></svg>
          (000)555-0142
        </li>
        <li>
          <svg viewBox="0 0 24 24" aria-hidden="true"><path d="M2 6l10 7 10-7V5H2zm0 2.4V19h20V8.4l-10 7z"/></svg>
          paul@dunmoreroofing-example.com
        </li>
        <li>
          <svg viewBox="0 0 24 24" aria-hidden="true"><path d="M12 2a10 10 0 100 20 10 10 0 000-20zm6.9 6h-3a15 15 0 00-1.4-3.9A8 8 0 0118.9 8zM12 4c.8 1.2 1.5 2.5 1.9 4h-3.8c.4-1.5 1.1-2.8 1.9-4zM4.3 14a8 8 0 010-4h3.4a16 16 0 000 4zm.8 2h3a15 15 0 001.4 3.9A8 8 0 015.1 16zm3-8h-3a8 8 0 014.4-3.9A15 15 0 008.1 8zM12 20c-.8-1.2-1.5-2.5-1.9-4h3.8c-.4 1.5-1.1 2.8-1.9 4zm2.3-6H9.7a14 14 0 010-4h4.6a14 14 0 010 4zm.2 5.9a15 15 0 001.4-3.9h3a8 8 0 01-4.4 3.9zm1.8-5.9a16 16 0 000-4h3.4a8 8 0 010 4z"/></svg>
          www.dunmoreroofing-example.com
        </li>
      </ul>
    </div>
  </div>
</body>
</html>
```